Real Estate business card for me

Business card for a realtor. I have just a few "must haves"... so I am hoping to get some great ideas back without my telling you what I want.

I just want something cool, appealing to the eye, modern-ish while still looking clean and professional. I'm a young-spirited 40 yo man. I don't wan the business card of a 23 year old or a 63 year old! haha

Industry/Entity Type

Real Estate Agent

Contact Information for Business Card

Whatever Wexford Calloway logo you use, it should be true WC purple color. Outside of that, color scheme is open to ideas.

Requirements
Must have
• Must include:
• Wexford Calloway, Pemberly Estates
• Dale Fenwick
• REALTORĀ®
• 555.417.2093
• HomesWithDale@mailbox-demo.com
Nice to have
• Can include my picture, but it doesn't have to. I saw a card the other day with a house sketch on the backside saying "Your referrals are the sincerest compliment I can receive". That was cool. I also saw a card which one side was just a full frame picture of me, info on reverse side. I like all those ideas as well, but definitely open to ANYTHING cool, a little different, stands out from the monotony of business cards realtors are passing around. It needs to have a Wexford logo on it somewhere, but I don't want it huge or the focal point. Im selling me, not the franchise. You can literally google Wexford Calloway Home Services and find all of the logos. Any of the main stream ones will work. They are typically a dark purple or dark purple and cream.
Should not have
• I do not want a huge logo presence.

```html
<!DOCTYPE html>
<html lang="en">
<head>
<meta charset="UTF-8">
<title>Dale Fenwick – Realtor Business Card</title>
<link rel="stylesheet" href="https://fonts.googleapis.com/css2?family=Lato:wght@300;400;700&display=swap">
<style>
  :root {
    --backdrop: #2b2b2d;
    --card: #1e1f21;
    --ink: #ececec;
    --ink-soft: #d6d6d6;
    --rule: #5a5b5e;
    --portrait-top: #1c1d20;
    --portrait-mid: #2a2b2f;
    --portrait-warm: #6b4a3c;
    --portrait-suit: #2e3036;
    --brand-purple: #6b2f5f;
    --brand-purple-edge: #8a4a7c;
  }
  * { box-sizing: border-box; margin: 0; padding: 0; }
  html, body {
    width: 1200px;
    height: 1108px;
    overflow: hidden;
    background: var(--backdrop);
    font-family: "Lato", sans-serif;
  }
  .sheet {
    width: 1200px;
    height: 1108px;
    display: flex;
    justify-content: center;
    align-items: center;
    gap: 60px;
  }
  .card {
    width: 420px;
    height: 735px;
    border-radius: 22px;
    background: var(--card);
    overflow: hidden;
    position: relative;
    box-shadow: 0 18px 40px rgba(0, 0, 0, 0.45);
  }
  .card-front .portrait {
    width: 100%;
    height: 100%;
    background:
      radial-gradient(ellipse 38% 26% at 62% 40%, rgba(107, 74, 60, 0.55) 0%, rgba(107, 74, 60, 0) 100%),
      linear-gradient(180deg, var(--portrait-top) 0%, var(--portrait-mid) 45%, var(--portrait-suit) 70%, var(--portrait-top) 100%);
  }
  .card-back {
    display: flex;
    flex-direction: column;
    align-items: center;
    padding-top: 280px;
    color: var(--ink);
    text-align: center;
  }
  .agent-name {
    font-weight: 700;
    font-size: 34px;
    letter-spacing: 0.5px;
    text-transform: uppercase;
  }
  .agent-title {
    font-weight: 300;
    font-size: 26px;
    letter-spacing: 1px;
    color: var(--ink-soft);
    margin-top: 2px;
  }
  .rule {
    width: 250px;
    height: 1px;
    background: var(--rule);
    margin: 14px 0;
  }
  .contact {
    font-weight: 400;
    font-size: 24px;
    line-height: 1.35;
    color: var(--ink-soft);
  }
  .contact-email { font-size: 21px; }
  .brokerage {
    display: flex;
    flex-direction: column;
    align-items: center;
    gap: 3px;
    color: var(--ink);
    font-weight: 400;
  }
  .brokerage-mark {
    width: 22px;
    height: 22px;
    background: var(--brand-purple);
    border: 1px solid var(--brand-purple-edge);
    border-radius: 50%;
    margin-bottom: 5px;
  }
  .brokerage-name { font-size: 15px; letter-spacing: 1px; text-transform: uppercase; }
  .brokerage-office { font-size: 14px; }
</style>
</head>
<body>
  <main class="sheet">
    <section class="card card-front">
      <div class="portrait" role="img" aria-label="Head-and-shoulders portrait photo of the realtor, smiling, in a dark suit jacket and open white shirt against a dark backdrop"></div>
    </section>
    <section class="card card-back">
      <h1 class="agent-name">Dale Fenwick</h1>
      <p class="agent-title">REALTOR®</p>
      <div class="rule"></div>
      <p class="contact">555.417.2093</p>
      <p class="contact contact-email">HomesWithDale@mailbox-demo.com</p>
      <div class="rule"></div>
      <div class="brokerage">
        <span class="brokerage-mark"></span>
        <span class="brokerage-name">Wexford Calloway</span>
        <span class="brokerage-office">Pemberly Estates</span>
      </div>
    </section>
  </main>
</body>
</html>
```